Business Card for a Jewellery Brand

Business card for an upscale jewellery brand. Attached is the brand logo and icon and color board. I am looking for two card versions: one for the founder and one is generic. The card should be elegant and convey upscale and premium feel. I am open to both square and rectangle card shapes.

Industry/Entity Type

Jewelry

Contact Information for Business Card

Two cards: (1) Sunela Parvaniya (Founder) (2) General
(1) Sunela Parvaniya card should have Name: Sunela Parvaniya, Title: Founder Email id: sunela@quiremo.com.au. Phone no: +61452913307
(2) Generic card should have Email id: info@quiremo.com.au. Phone no: +61436207518

Requirements
Must have
• Workmark
• ICON
• Phone no
• Email ID
• ABN: 58219740312 (Note: ABN is Business number in Australia)
• Website: www.quiremo.com.au
• Instagram: quiremo_jewellery
• Facebook: @quiremojewellery
Nice to have
• Tagline

```html
<!DOCTYPE html>
<html lang="en">
<head>
<meta charset="utf-8">
<title>Quiremo – Business Cards</title>
<link rel="stylesheet" href="https://fonts.googleapis.com/css2?family=Raleway:wght@400;500;600&display=swap">
<style>
  :root {
    --gold: #b99469;
    --gold-light: #c9a77f;
    --grey-text: #9b9b9b;
    --card-white: #ffffff;
    --marble-a: #f4f5f6;
    --marble-b: #e6e8ea;
    --page: #ffffff;
  }
  * { box-sizing: border-box; margin: 0; padding: 0; }
  html, body {
    width: 1200px;
    height: 738px;
    overflow: hidden;
    background: var(--page);
    font-family: "Raleway", sans-serif;
  }
  .canvas { position: relative; width: 1200px; height: 738px; }

  .card {
    position: absolute;
    top: 138px;
    width: 465px;
    height: 462px;
    background: var(--card-white);
    border: 1px solid #ececec;
    overflow: hidden;
  }
  .card--front { left: 92px; }
  .card--back { left: 643px; }

  /* front */
  .marble-surface {
    position: absolute;
    inset: 0;
    background:
      radial-gradient(ellipse at 70% 20%, var(--marble-b) 0%, transparent 55%),
      radial-gradient(ellipse at 25% 75%, var(--marble-b) 0%, transparent 50%),
      linear-gradient(135deg, var(--marble-a), #eef0f1 50%, var(--marble-a));
  }
  .brand-mark__circle {
    position: absolute;
    left: 50%;
    top: 112px;
    width: 100px;
    height: 100px;
    margin-left: -50px;
    border: 2px solid var(--gold);
    border-radius: 50%;
  }
  .brand-mark__name {
    position: absolute;
    left: 0;
    right: 0;
    top: 240px;
    text-align: center;
    font-weight: 500;
    font-size: 42px;
    letter-spacing: 0.2em;
    padding-left: 0.2em;
    color: var(--gold);
    line-height: 1;
  }
  .social {
    position: absolute;
    left: 121px;
    top: 360px;
    list-style: none;
  }
  .social__item {
    display: flex;
    align-items: center;
    height: 34px;
    margin-bottom: 12px;
    font-size: 24px;
    color: var(--gold-light);
    white-space: nowrap;
  }
  .social__square {
    width: 34px;
    height: 34px;
    background: var(--gold);
    border-radius: 3px;
    margin-right: 12px;
    flex: none;
  }

  /* back */
  .person {
    position: absolute;
    left: 64px;
    top: 76px;
  }
  .person__name {
    font-size: 27px;
    font-weight: 600;
    color: var(--gold);
    line-height: 1.2;
    white-space: nowrap;
  }
  .person__title {
    font-size: 21px;
    color: var(--grey-text);
    line-height: 1.2;
  }
  .divider {
    position: absolute;
    left: 65px;
    top: 270px;
    width: 197px;
    height: 1px;
    background: var(--gold);
  }
  .contact {
    position: absolute;
    left: 40px;
    top: 287px;
    list-style: none;
  }
  .contact__item {
    display: flex;
    align-items: center;
    height: 30px;
    font-size: 21px;
    color: var(--grey-text);
    white-space: nowrap;
  }
  .contact__icon {
    width: 18px;
    height: 18px;
    margin-right: 6px;
    flex: none;
  }
  .contact__item--abn { padding-left: 24px; font-size: 19px; }
</style>
</head>
<body>
<main class="canvas">

  <section class="card card--front" aria-label="Card front">
    <div class="marble-surface" role="img" aria-label="White marble texture background with soft grey veins"></div>
    <span class="brand-mark__circle" aria-hidden="true"></span>
    <p class="brand-mark__name">QUIREMO</p>
    <ul class="social">
      <li class="social__item"><span class="social__square"></span>quiremo_jewellery</li>
      <li class="social__item"><span class="social__square"></span>@quiremojewellery</li>
    </ul>
  </section>

  <section class="card card--back" aria-label="Card back">
    <div class="person">
      <p class="person__name">Sunela Parvaniya</p>
      <p class="person__title">Founder</p>
    </div>
    <div class="divider"></div>
    <ul class="contact">
      <li class="contact__item">
        <svg class="contact__icon" viewBox="0 0 20 20" aria-hidden="true">
          <rect x="5" y="2" width="10" height="16" rx="1.5" fill="none" stroke="var(--gold)" stroke-width="1.5"/>
          <line x1="9" y1="15.5" x2="11" y2="15.5" stroke="var(--gold)" stroke-width="1.2"/>
        </svg>+61452913307</li>
      <li class="contact__item">
        <svg class="contact__icon" viewBox="0 0 20 20" aria-hidden="true">
          <rect x="1" y="5" width="18" height="11" fill="var(--gold)"/>
          <polyline points="1,5 10,12 19,5" fill="none" stroke="#fff" stroke-width="1.3"/>
        </svg>sunela@quiremo.com.au</li>
      <li class="contact__item">
        <svg class="contact__icon" viewBox="0 0 20 20" aria-hidden="true">
          <g fill="none" stroke="var(--gold)" stroke-width="1.4">
            <circle cx="10" cy="10" r="8"/>
            <ellipse cx="10" cy="10" rx="3.5" ry="8"/>
            <line x1="2" y1="10" x2="18" y2="10"/>
            <line x1="3.5" y1="6" x2="16.5" y2="6"/>
            <line x1="3.5" y1="14" x2="16.5" y2="14"/>
          </g>
        </svg>www.quiremo.com.au</li>
      <li class="contact__item contact__item--abn">ABN: 58219740312</li>
    </ul>
  </section>

</main>
</body>
</html>
```